Package Design - Disposable Face Towel

Hi,

We are needing assistance with graphic design on our box/carton/package.

The attached image that is white is our biggest competitor.

Our brand is "VELMORA BATH CO." Please see the logo we uploaded.

Oder we have in mind for front of box:

Logo
LARGE TOWELS
50 Count
Ultra Soft| 100% USDA Bio-Based|100% Eucalyptus Viscose | Vegan
VELMORABATHCO.COM

We like medium to dark blue on most of the box, with white and minimal hot pink or salmon. Something that is sharp, modern, and stands out from our competitors.

Box dimensions are: 6.25 x 5.25 x 4.75 inches

This will be 1 of many design projects.

Target Market(s)

Female Beauty Products

Font styles to use
Serif
Sans Serif

Colors
0054AA
0677BA
7BADD7
CADEEF
E8F1F8
EB3D1F
EC4F4E
F09395
F8D3D4
FCEDEE

Requirements
Must have
• Needs to look sharp and modern

```html
<!DOCTYPE html>
<html lang="en">
<head>
<meta charset="utf-8">
<title>Velmora Bath Co. – Large Towels Packaging</title>
<link rel="stylesheet" href="https://fonts.googleapis.com/css2?family=Marcellus&family=Lora:wght@400&family=Roboto:wght@400&display=swap">
<style>
  :root {
    --blue-deep: #0054AA;
    --blue-mid: #0677BA;
    --blue-light: #7BADD7;
    --blue-pale: #CADEEF;
    --blue-mist: #E8F1F8;
    --accent: #EC4F4E;
    --accent-soft: #F8D3D4;
    --white: #FFFFFF;
    --page: #FFFFFF;
    --ink-dark: #1F3550;
  }
  * { box-sizing: border-box; margin: 0; padding: 0; }
  html, body { width: 1200px; height: 2688px; overflow: hidden; background: var(--page); }
  .canvas { position: relative; width: 1200px; height: 2688px; }

  /* Colour scheme */
  .palette { position: absolute; left: 695px; top: 78px; display: flex; gap: 8px; }
  .swatch { width: 93px; }
  .swatch-chip { height: 162px; }
  .swatch-code { font: 400 9px "Roboto", sans-serif; color: var(--ink-dark); text-align: center; margin-top: 5px; }
  .palette-caption { position: absolute; left: 695px; top: 262px; font: 400 10px "Roboto", sans-serif; color: var(--ink-dark); }

  /* Flat top label */
  .top-label { position: absolute; left: 413px; top: 340px; width: 677px; height: 513px; background: var(--blue-deep); }
  .top-label-face { position: absolute; left: 69px; top: 0; width: 539px; height: 513px; background: var(--blue-mid);
    display: flex; flex-direction: column; align-items: center; justify-content: center; }

  .brand-name { font: 400 42px "Marcellus", serif; color: var(--white); letter-spacing: 0.5px; white-space: nowrap; }
  .product-name { font: 400 24px "Marcellus", serif; color: var(--white); letter-spacing: 1.5px; white-space: nowrap; }
  .top-label-face .product-name { margin-top: 22px; color: var(--accent-soft); }

  /* Flat box front */
  .box-front { position: absolute; background: var(--blue-mid); }
  .box-front.view-open { left: 372px; top: 1000px; width: 646px; height: 560px; }
  .box-front.view-full { left: 306px; top: 2020px; width: 584px; height: 420px; }

  .dispenser-card { position: absolute; background: var(--blue-deep); display: flex; align-items: center; justify-content: center; }
  .view-open .dispenser-card { left: 66px; top: 0; width: 514px; height: 290px; }
  .view-open .dispenser-card .brand-name { font-size: 36px; }

  .towel-window { position: absolute; left: 126px; top: 12px; width: 394px; height: 190px; background: var(--white); }

  .dispenser-slot { position: absolute; left: 0; }
  .view-open .dispenser-slot { top: 250px; width: 646px; height: 90px; }
  .view-full .dispenser-slot { top: 170px; width: 584px; height: 70px; }

  .front-copy { position: absolute; left: 0; width: 100%; text-align: center; }
  .view-open .front-copy { top: 370px; }
  .view-full .front-copy { top: 262px; }
  .view-open .product-name { font-size: 28px; letter-spacing: 2px; }
  .view-full .product-name { font-size: 22px; letter-spacing: 1.5px; }
  .features { font: 400 15px/25px "Lora", serif; color: var(--blue-mist); letter-spacing: 0.6px; margin-top: 22px; }
  .view-full .features { font-size: 13px; line-height: 21px; margin-top: 16px; }

  .url-band { position: absolute; left: 0; bottom: 0; width: 100%; background: var(--blue-deep);
    display: flex; align-items: center; justify-content: center; font: 400 17px "Lora", serif; color: var(--white); letter-spacing: 2.5px; }
  .view-open .url-band { height: 50px; }
  .view-full .url-band { height: 44px; font-size: 15px; }

  .count-badge { position: absolute; width: 78px; height: 78px; }
  .view-open .count-badge { right: 38px; top: 464px; }
  .view-full .count-badge { right: 50px; top: 330px; width: 62px; height: 62px; }

  /* Folded dispenser card, laid flat */
  .lid-card { position: absolute; left: 450px; top: 1815px; width: 372px; height: 180px; background: var(--blue-deep);
    display: flex; align-items: center; justify-content: center; }
  .lid-card .brand-name { font-size: 28px; }
</style>
</head>
<body>
<main class="canvas">

  <section class="palette" aria-label="Blue and pink colour scheme">
    <div class="swatch"><div class="swatch-chip" style="background:var(--blue-deep)"></div><p class="swatch-code">#0054AA</p></div>
    <div class="swatch"><div class="swatch-chip" style="background:var(--blue-mid)"></div><p class="swatch-code">#0677BA</p></div>
    <div class="swatch"><div class="swatch-chip" style="background:var(--blue-pale)"></div><p class="swatch-code">#CADEEF</p></div>
    <div class="swatch"><div class="swatch-chip" style="background:var(--accent)"></div><p class="swatch-code">#EC4F4E</p></div>
  </section>
  <p class="palette-caption">Blue And Pink Color Scheme</p>

  <section class="top-label">
    <div class="top-label-face">
      <p class="brand-name">VELMORA BATH CO.</p>
      <p class="product-name">LARGE TOWELS</p>
    </div>
  </section>

  <!-- Box front with dispenser card raised -->
  <section class="box-front view-open">
    <div class="dispenser-card"><p class="brand-name">VELMORA BATH CO.</p></div>
    <svg class="dispenser-slot" viewBox="0 0 646 90" preserveAspectRatio="none">
      <path d="M45 10 H270 L300 50 H370 L400 10 H600 Q620 10 620 35 Q620 60 600 60 H45 Q25 60 25 35 Q25 10 45 10 Z"
            fill="#7BADD7" stroke="#CADEEF" stroke-width="2"/>
      <path d="M270 10 L300 50 H370 L400 10 Z" fill="#0054AA"/>
    </svg>
    <div class="front-copy">
      <p class="product-name">LARGE TOWELS</p>
      <p class="features">Ultra Soft | 100% USDA Bio–Based<br>100% Eucalyptus Viscose | Vegan</p>
    </div>
    <div class="url-band">www.velmorabathco.com</div>
    <svg class="count-badge" viewBox="0 0 78 78">
      <rect x="14" y="14" width="50" height="50" rx="5" transform="rotate(45 39 39)" fill="#EC4F4E"/>
      <text x="39" y="38" text-anchor="middle" font-family="Lora, serif" font-size="20" fill="#FFFFFF">50</text>
      <text x="39" y="52" text-anchor="middle" font-family="Lora, serif" font-size="11" fill="#FFFFFF">Count</text>
    </svg>
  </section>

  <!-- Dispenser card and box front with towel window -->
  <section class="lid-card"><p class="brand-name">VELMORA BATH CO.</p></section>

  <section class="box-front view-full">
    <div class="towel-window"></div>
    <svg class="dispenser-slot" viewBox="0 0 584 70" preserveAspectRatio="none">
      <path d="M140 8 H290 L305 32 H370 L385 8 H520 Q535 8 535 22 Q535 36 520 36 H140 Z"
            fill="#7BADD7" stroke="#CADEEF" stroke-width="2"/>
    </svg>
    <div class="front-copy">
      <p class="product-name">LARGE TOWELS</p>
      <p class="features">Ultra Soft | 100% USDA Bio–Based<br>100% Eucalyptus Viscose | Vegan</p>
    </div>
    <div class="url-band">www.velmorabathco.com</div>
    <svg class="count-badge" viewBox="0 0 78 78">
      <rect x="14" y="14" width="50" height="50" rx="5" transform="rotate(45 39 39)" fill="#EC4F4E"/>
      <text x="39" y="38" text-anchor="middle" font-family="Lora, serif" font-size="20" fill="#FFFFFF">50</text>
      <text x="39" y="52" text-anchor="middle" font-family="Lora, serif" font-size="11" fill="#FFFFFF">Count</text>
    </svg>
  </section>

</main>
</body>
</html>
```